Design and Renovation Company Luxury Business Card

I want to create a luxury business card for a Design and Renovation Firm . We will use our current logo. The company name is 528BUILDA. We do not want anything standard. We need a very unique concept.
Please see uploaded inspiration. I really like the textured paper option. I would like the card to be thick with debossing, and/or embossing options. The logo has orange in it but I would like to see the card with and without the orange. I think the orange may make the company feel less high-end. The goal is to elevate the logo not match its vibe per se of the logo. We want something very unique, not standard at all!
I would like a space for :
Logo,
Name,
Position,
Email,
Office number,
Website Address,
Business Address,
Thank you!
Have fun!
Target Market(s)
Home owners Age 35 +
Industry/Entity Type
Design and Renovation
Contact Information for Business Card
Logo, Name, Position, Email, Office number, Website Address, Business Address,.
Colors
Designer to choose colors to be used in the design.
Requirements
Must have
- A luxury designer feel. Must be black or dark grey but open to other luxury ideas.
Nice to have
- Gold, silver, black embossing or debossing. Textured paper design.
Should not have
- A cheap look and feel.

```html
<!DOCTYPE html>
<html lang="en">
<head>
<meta charset="UTF-8">
<title>528BUILDA Business Card</title>
<link href="https://fonts.googleapis.com/css2?family=Open+Sans:wght@400;600;700&display=swap" rel="stylesheet">
<style>
  :root {
    --bg: #2a2d31;
    --card-black: #141414;
    --card-white: #ffffff;
    --accent: #f39a1e;
    --ink: #1c1c1c;
    --light: #f2f2f2;
  }
  * { margin: 0; padding: 0; box-sizing: border-box; }
  html, body { width: 1200px; height: 900px; overflow: hidden; }
  body {
    background: var(--bg);
    font-family: "Open Sans", sans-serif;
    position: relative;
  }
  .card {
    position: absolute;
    left: 320px;
    width: 560px;
    height: 320px;
    border-radius: 22px;
    overflow: hidden;
    box-shadow: 0 10px 30px rgba(0,0,0,0.45);
  }
  .card-back { top: 90px; background: var(--card-black); }
  .card-front { top: 490px; background: var(--card-white); }

  .company-name {
    position: absolute;
    font-family: "Open Sans", sans-serif;
    font-weight: 600;
    line-height: 1;
    white-space: nowrap;
  }
  .tagline {
    position: absolute;
    font-family: "Open Sans", sans-serif;
    font-weight: 400;
    white-space: nowrap;
  }

  /* back */
  .card-back .company-name {
    left: 0; right: 0; top: 124px;
    text-align: center;
    font-size: 50px;
    color: var(--light);
  }
  .card-back .tagline {
    left: 0; right: 0; top: 188px;
    text-align: center;
    font-size: 13px;
    letter-spacing: 2px;
    color: var(--light);
  }

  /* front */
  .front-shape { position: absolute; inset: 0; }
  .card-front .company-name { left: 36px; top: 38px; font-size: 32px; color: var(--ink); }
  .card-front .tagline { left: 37px; top: 78px; font-size: 9.5px; letter-spacing: 1.5px; color: var(--ink); }

  .contact {
    position: absolute;
    left: 290px;
    top: 104px;
    padding-left: 14px;
    border-left: 1.5px solid var(--accent);
    color: var(--ink);
  }
  .contact .name { font-size: 22px; font-weight: 700; color: var(--accent); line-height: 1.1; }
  .contact .role { font-size: 13px; margin-bottom: 8px; }
  .contact .address { font-size: 12.5px; line-height: 1.35; margin-bottom: 6px; }
  .contact .row { display: flex; align-items: center; font-size: 12.5px; line-height: 1.5; }
  .contact .row svg { width: 11px; height: 11px; margin-right: 7px; flex: none; }
</style>
</head>
<body>

<section class="card card-back" aria-label="Card back">
  <div class="company-name">528BUILDA</div>
  <div class="tagline">Design and Renovation Firm</div>
</section>

<section class="card card-front" aria-label="Card front">
  <svg class="front-shape" viewBox="0 0 560 320" width="560" height="320" aria-hidden="true">
    <path d="M0 130 C 70 250, 250 305, 560 322 L560 320 L0 320 Z" fill="var(--card-black)"/>
    <path d="M44 120 C 110 230, 270 292, 480 320" fill="none" stroke="var(--accent)" stroke-width="3"/>
  </svg>

  <div class="company-name">528BUILDA</div>
  <div class="tagline">Design and Renovation Firm</div>

  <div class="contact">
    <div class="name">Daniel Varga</div>
    <div class="role">Managing Director</div>
    <div class="address">415 Maple Grove Ave. #112<br>Riverton, OH 43217</div>
    <div class="row">
      <svg viewBox="0 0 12 12"><path d="M2.5 1 L4.5 1 L5.3 3.6 L4 4.6 C4.7 6 6 7.3 7.4 8 L8.4 6.7 L11 7.5 L11 9.5 C11 10.3 10.3 11 9.5 11 C5 11 1 7 1 2.5 C1 1.7 1.7 1 2.5 1 Z" fill="var(--accent)"/></svg>
      555-318-0247
    </div>
    <div class="row">
      <svg viewBox="0 0 12 12"><rect x="1" y="2.5" width="10" height="7" fill="var(--accent)"/><path d="M1 2.5 L6 6.5 L11 2.5" fill="none" stroke="#fff" stroke-width="1"/></svg>
      info@528builda-studio.com
    </div>
    <div class="row">
      <svg viewBox="0 0 12 12"><circle cx="6" cy="6" r="4.8" fill="none" stroke="var(--accent)" stroke-width="1.3"/><path d="M1.2 6 H10.8 M6 1.2 C3.8 4 3.8 8 6 10.8 M6 1.2 C8.2 4 8.2 8 6 10.8" fill="none" stroke="var(--accent)" stroke-width="1"/></svg>
      www.528builda-studio.com
    </div>
  </div>
</section>

</body>
</html>
```